I need a business card design for a new business based in South West Australia.
I specialize in residential window cleaning & general handyman maintenance.

Dale Marsh - 412 SILVER HAWK DETAILING
- Window Cleaning
- House Maintenance

```html
<!DOCTYPE html>
<html lang="en">
<head>
<meta charset="utf-8">
<title>Silver Hawk Detailing – Business Card</title>
<link href="https://fonts.googleapis.com/css2?family=Open+Sans:wght@400;600&display=swap" rel="stylesheet">
<style>
  :root {
    --bg: #e9e6e1;
    --card-black: #161616;
    --band-blue: #4f95d0;
    --glass-light: #c9d6e2;
    --glass-dark: #7d93a8;
    --text-white: #ffffff;
    --text-soft: #e4e4e4;
  }
  * { box-sizing: border-box; margin: 0; padding: 0; }
  html, body {
    width: 1200px; height: 892px; overflow: hidden;
    background: var(--bg);
    font-family: "Open Sans", Arial, sans-serif;
  }
  .sheet {
    width: 1200px; height: 892px;
    display: flex; flex-direction: column;
    align-items: center; justify-content: center; gap: 36px;
  }
  .card {
    position: relative;
    width: 700px; height: 400px;
    border-radius: 6px; overflow: hidden;
    box-shadow: 0 6px 18px rgba(0,0,0,0.18);
    background: var(--card-black);
  }
  .card-art { position: absolute; inset: 0; width: 100%; height: 100%; }
  .brand {
    position: absolute; right: 40px; top: 48px;
    text-align: right; color: var(--text-white);
  }
  .brand-name {
    font-size: 31px; font-weight: 400; letter-spacing: 0.5px; line-height: 1;
  }
  .services { list-style: none; margin-top: 22px; }
  .services li {
    font-size: 20px; color: var(--text-soft); line-height: 1; margin-bottom: 18px;
    display: flex; justify-content: flex-end; align-items: center; gap: 16px;
  }
  .services li::after {
    content: ""; width: 9px; height: 9px; border-radius: 50%;
    background: var(--text-white);
  }
  .contact {
    position: absolute; left: 250px; bottom: 44px; color: var(--text-white);
  }
  .contact-name { font-size: 31px; font-weight: 600; line-height: 1.1; }
  .contact-phone {
    margin-top: 12px; font-size: 21px; color: var(--text-soft);
    display: flex; align-items: center; gap: 14px;
  }
  .phone-icon {
    width: 20px; height: 20px; background: var(--text-white); border-radius: 3px;
    display: flex; align-items: center; justify-content: center;
  }
</style>
</head>
<body>
<main class="sheet">

  <section class="card card-front">
    <svg class="card-art" viewBox="0 0 700 400" preserveAspectRatio="none">
      <defs>
        <linearGradient id="glassFront" x1="0" y1="0" x2="1" y2="1">
          <stop offset="0" stop-color="var(--glass-light)"/>
          <stop offset="1" stop-color="var(--glass-dark)"/>
        </linearGradient>
      </defs>
      <rect width="700" height="400" fill="url(#glassFront)" role="img" aria-label="Photo of a squeegee wiping soapy window glass"/>
      <path d="M290 0 Q170 230 130 400 L700 400 L700 0 Z" fill="var(--band-blue)"/>
      <path d="M380 0 Q260 230 225 400 L700 400 L700 0 Z" fill="var(--card-black)"/>
    </svg>
    <div class="brand">
      <h1 class="brand-name">SILVER HAWK DETAILING</h1>
      <ul class="services">
        <li>House Maintenance</li>
        <li>Window Cleaning</li>
      </ul>
    </div>
    <div class="contact">
      <p class="contact-name">Dale Marsh</p>
      <p class="contact-phone">
        <span class="phone-icon">
          <svg width="12" height="12" viewBox="0 0 24 24"><path d="M6.6 10.8a15 15 0 0 0 6.6 6.6l2.2-2.2a1 1 0 0 1 1-.25 11 11 0 0 0 3.6.6 1 1 0 0 1 1 1V20a1 1 0 0 1-1 1A17 17 0 0 1 3 4a1 1 0 0 1 1-1h3.5a1 1 0 0 1 1 1 11 11 0 0 0 .6 3.6 1 1 0 0 1-.25 1z" fill="#161616"/></svg>
        </span>
        0400 128 546
      </p>
    </div>
  </section>

  <section class="card card-back">
    <svg class="card-art" viewBox="0 0 700 400" preserveAspectRatio="none">
      <defs>
        <linearGradient id="glassBack" x1="0" y1="0" x2="1" y2="1">
          <stop offset="0" stop-color="var(--glass-light)"/>
          <stop offset="1" stop-color="var(--glass-dark)"/>
        </linearGradient>
      </defs>
      <rect width="700" height="400" fill="url(#glassBack)" role="img" aria-label="Photo of a squeegee wiping soapy window glass"/>
      <path d="M290 0 Q170 230 130 400 L700 400 L700 0 Z" fill="var(--band-blue)"/>
      <path d="M380 0 Q260 230 225 400 L700 400 L700 0 Z" fill="var(--card-black)"/>
    </svg>
    <div class="brand" style="top: 120px;">
      <h2 class="brand-name">SILVER HAWK DETAILING</h2>
      <ul class="services">
        <li>House Maintenance</li>
        <li>Window Cleaning</li>
      </ul>
    </div>
  </section>

</main>
</body>
</html>
```